Health Wellbeing Beauty online Shop

I have attached a full spec, however in summary this is a new business startup selling skincare products.

We need a web design for new wellbeing website, selling skincare products so need an eCommerce solution . On the home page I would like these faces to dissolve into each other on a loop or use a honeycomb style transation.
You will need the option of being able to log into an account, either through lumigram, vexora, chirplo or create an account. For created accounts, obviously need the facility to be able to reset passwords, see previous orders, track current order, and maintain favourites.
It should be PC, mobile and tablet friendly.

Look and Feel
It should be an elegant, modern, professional, trendy, unisex website. It should look clean and calm. Am happy to try interesting and slightly unusual designs. I would also like to have chat functionality, either powered by talvuNchat or by Quo 58.
Websites I like are
https://www.nobel-radiance.example.co.uk/
https://www.mereminerals.example.co.uk/
http://www.brightdermis.example.com/

PLEASE DO USE YOUR KNOWELDGE OF WHAT WORKS FOR WEB DESIGN. YOU’RE THE EXPERT AND NEED YOUR EXPERTISE. CARTE BLANCHE TO DESIGN AS YOU SEE FIT. Please be creative, I need my site to stand out from the crowd.

Target Market(s)

Target Market
Middle aged women are our most common client, however, younger patients, both male and female, will often visit the site. In summary, I would like the site to appeal to all age brackets.

Industry/Entity Type

Business

Coding

Coded - Design and coding required

Number of Pages Required

4 page

Requirements
Must have
• Need shop to be exactly like shop on this link http://www.brightdermis.example.com/
Nice to have
• i would like something unique and creative

```html
<!DOCTYPE html>
<html lang="en">
<head>
<meta charset="utf-8">
<title>Lunessa – Skin Lightening Shop</title>
<link rel="stylesheet" href="https://fonts.googleapis.com/css2?family=Titillium+Web:wght@300;400;600&family=Open+Sans:wght@400;600&display=swap">
<style>
:root{
  --ink:#1f1f1f;
  --ink-2:#262626;
  --gold:#c19a66;
  --gold-dark:#a9885b;
  --gold-text:#a88050;
  --bronze:#9c7b52;
  --card:#ededed;
  --line:#d8d8d8;
  --white:#ffffff;
  --muted:#6b6b6b;
}
*{box-sizing:border-box;margin:0;padding:0}
html,body{width:1200px;height:3673px;overflow:hidden}
body{position:relative;background:var(--white);font-family:"Open Sans",Arial,sans-serif;color:var(--ink)}
.abs{position:absolute}

/* header */
.site-header{left:0;top:0;width:1200px;height:167px;background:var(--ink)}
.brand{left:159px;top:12px;width:98px;height:98px;border:2px solid var(--gold);border-radius:50%;display:flex;align-items:center;justify-content:center;color:var(--gold);font-family:"Titillium Web",sans-serif;font-size:19px;font-weight:400;letter-spacing:1px}
.utility{top:28px;left:745px;display:flex;gap:28px;align-items:center;color:#d8d8d8;font-size:13px}
.utility span{display:flex;align-items:center;gap:8px}
.socials{top:97px;left:918px;display:flex;gap:9px}
.socials i{display:block;width:22px;height:22px;border-radius:50%;background:var(--gold-dark)}

.main-nav{left:0;top:167px;width:1200px;height:58px;background:linear-gradient(#c9b083,#a98d63)}
.main-nav a{position:absolute;top:17px;color:var(--white);font-size:15px;text-decoration:none;font-family:"Titillium Web",sans-serif}

/* hero */
.hero{left:0;top:225px;width:1200px;height:610px;background:linear-gradient(100deg,#dcdcdc 0%,#cfc6b8 35%,#d7b98b 55%,#e6e3df 80%,#dedede 100%)}
.hero-card{left:98px;top:656px;width:380px;height:179px;background:var(--ink);padding:30px 24px;color:var(--white)}
.hero-card h1{font-family:"Titillium Web",sans-serif;font-weight:300;font-size:31px;word-spacing:10px;margin-bottom:14px}
.hero-card p{font-size:12px;line-height:20px;color:#e2e2e2}

/* products */
.section-title{width:1200px;left:0;text-align:center;font-family:"Titillium Web",sans-serif;font-weight:300;font-size:62px;color:var(--bronze)}
.filters{left:98px;top:989px;width:264px}
.filters .refine{height:40px;background:var(--gold);color:var(--white);font-size:12px;padding:12px 16px;display:flex;justify-content:space-between}
.filters .names{height:306px;border:1px solid var(--line);padding:14px 20px}
.filters .names h4{font-size:12px;font-weight:400;margin-bottom:20px}
.filters .names li{list-style:none;display:flex;align-items:center;gap:12px;font-size:11px;color:#9a9a9a;height:26px}
.filters .names li i{width:15px;height:15px;border:1px solid #c8c8c8}
.filter-row{height:37px;background:var(--ink-2);color:var(--white);font-size:12px;padding:11px 16px;display:flex;justify-content:space-between;margin-top:9px}

.product{width:219px;height:424px}
.product .shot{background:var(--card);border:1px solid #e2e2e2;position:absolute;left:0;top:0;width:219px;height:424px}
.product .thumb{position:absolute;left:40px;top:16px;width:140px;height:190px;background:linear-gradient(#6b3a22,#3c1f12);border-radius:14px 14px 6px 6px}
.product .thumb.box{background:linear-gradient(135deg,#f2f2f2,#c9c9c9);height:120px;top:60px;border-radius:3px}
.product .rating{position:absolute;left:34px;top:236px;display:flex;gap:2px;align-items:center;font-size:10px;color:#8a8a8a}
.product .rating b{width:13px;height:13px;background:var(--ink);display:block}
.product .rating b.on{background:var(--gold)}
.product .rating span{margin-left:14px}
.product h3{position:absolute;top:272px;width:219px;text-align:center;font-size:12.5px;font-weight:600}
.product .cat{position:absolute;top:298px;width:219px;text-align:center;font-size:11px;color:var(--gold-text)}
.product .price{position:absolute;top:320px;width:219px;text-align:center;font-size:14px}
.product .quick{position:absolute;left:50px;top:356px;width:120px;height:44px;background:var(--ink-2);color:var(--white);font-size:12px;font-weight:600;text-align:center;line-height:44px}
.add-cart{width:120px;height:45px;background:var(--gold);color:var(--white);font-size:12px;font-weight:600;text-align:center;line-height:45px;letter-spacing:.5px}

/* contact */
.contact{left:0;top:2040px;width:1200px;height:537px;background:linear-gradient(90deg,#c9ccd0 0%,#e6e9ee 40%,#eef0f2 100%)}
.contact-photo{left:0;top:2040px;width:441px;height:537px;background:linear-gradient(90deg,#a4a6a8,#cbbcae 55%,#d6d9dc)}
.contact-title{left:620px;top:2068px;font-family:"Titillium Web",sans-serif;font-weight:400;font-size:44px;color:var(--ink)}
.contact-lead{left:453px;top:2143px;font-size:12.5px}
.contact-col{top:2185px;font-size:12.5px;line-height:24px}
.contact-col b{font-weight:600}
.contact-form{left:433px;top:2273px;width:664px;height:304px;background:var(--ink)}
.contact-form p{position:absolute;left:80px;top:22px;font-size:12.5px;color:var(--gold)}
.field{border:1px solid #6e5a3c;color:#8a7455;font-family:Georgia,serif;font-style:italic;font-size:12px;padding:13px 14px}
.send{left:678px;top:2540px;width:155px;height:37px;background:var(--gold);color:var(--white);font-size:13px;font-weight:600;text-align:center;line-height:37px}

/* about */
.about{left:0;top:2577px;width:1200px;height:594px;background:linear-gradient(90deg,#b48d5c 0%,#c8a273 40%,#d7b287 70%,#caa374 100%)}
.about-photo{left:760px;top:2577px;width:440px;height:594px;background:radial-gradient(ellipse at 55% 40%,rgba(240,214,176,.75),rgba(200,162,115,0) 70%)}
.about-title{left:0;width:1200px;top:2636px;text-align:center;font-family:"Titillium Web",sans-serif;font-weight:300;font-size:62px;line-height:1.1;color:var(--white)}
.about-box{left:306px;top:2762px;width:595px;height:299px;background:var(--white);padding:44px 50px;text-align:center;font-size:12px;line-height:19px;color:#333}
.about-box p+p{margin-top:19px}

/* footer */
.footer{left:0;top:3171px;width:1200px;height:265px;background:#222}
.foot-col{top:3218px;color:#d0d0d0;font-size:11.5px;line-height:17px}
.foot-col h5{color:var(--white);font-size:13px;font-weight:600;margin-bottom:26px}
.pill{display:inline-block;margin-top:18px;padding:0 26px;height:32px;line-height:32px;border-radius:16px;background:var(--gold);color:var(--white);font-size:10.5px;font-weight:600}
.email{margin-top:16px;width:206px;height:34px;border-radius:17px;background:var(--white);color:#aaa;font-size:10.5px;padding:9px 16px}
.bottom{left:0;top:3436px;width:1200px;height:237px;background:#1b1b1b;text-align:center;color:var(--white)}
.bottom h6{margin-top:50px;font-size:16px;font-weight:600}
.follow-icons{display:flex;justify-content:center;gap:22px;margin-top:26px}
.follow-icons i{display:block;width:26px;height:26px;border-radius:50%;border:1px solid #555}
.bottom small{display:block;margin-top:30px;font-size:11px;color:#888}
</style>
</head>
<body>

<header class="abs site-header"></header>
<div class="abs brand">Lunessa</div>
<div class="abs utility">
  <span>Search
    <svg width="16" height="16" viewBox="0 0 16 16"><circle cx="6.5" cy="6.5" r="5" fill="none" stroke="#c19a66" stroke-width="1.5"/><line x1="10" y1="10" x2="15" y2="15" stroke="#c19a66" stroke-width="1.5"/></svg></span>
  <span>Sign In
    <svg width="16" height="18" viewBox="0 0 16 18"><circle cx="8" cy="5" r="4" fill="#c19a66"/><path d="M1 18c0-5 3-7 7-7s7 2 7 7z" fill="#c19a66"/></svg></span>
  <span>Shopping Cart
    <svg width="22" height="18" viewBox="0 0 22 18"><path d="M1 2h4l3 10h10l3-7H7" fill="none" stroke="#c19a66" stroke-width="1.5"/><circle cx="9" cy="15.5" r="1.6" fill="#c19a66"/><circle cx="17" cy="15.5" r="1.6" fill="#c19a66"/></svg></span>
</div>
<div class="abs socials"><i></i><i></i><i></i><i></i><i></i></div>

<nav class="abs main-nav">
  <a style="left:159px">Skin Lightening Tablets</a>
  <a style="left:345px">Skin Lightening Creams</a>
  <a style="left:536px">Skin Lightening Soaps</a>
  <a style="left:745px">Skin Lightening Vials</a>
  <a style="left:930px">Contact</a>
  <a style="left:1009px">About Us</a>
</nav>

<section class="abs hero" role="img" aria-label="Portrait photo of a smiling young woman with long blonde hair"></section>
<div class="abs hero-card">
  <h1>Enhance Enrich Engage</h1>
  <p>Our range of hair services includes everything your hair needs and would ever need, want to try a new hair color? a new hairstyle that suits you the best? or your hair needs...</p>
</div>

<h2 class="abs section-title" style="top:858px">Our Products</h2>

<aside class="abs filters">
  <div class="refine"><span>REFINE BY</span>
    <svg width="12" height="12" viewBox="0 0 12 12"><path d="M2 8l4-4 4 4" fill="none" stroke="#fff" stroke-width="1.6"/></svg></div>
  <div class="names">
    <h4>Name</h4>
    <ul>
      <li><i></i>Beachwear</li><li><i></i>tickedBlazers</li><li><i></i>tickedCardigans</li>
      <li><i></i>tickedCoats</li><li><i></i>tickedDresses</li><li><i></i>tickedHats</li>
      <li><i></i>tickedHoodies</li><li><i></i>tickedJackets</li>
    </ul>
  </div>
  <div class="filter-row">Top Sellers<svg width="12" height="12" viewBox="0 0 12 12"><path d="M2 4l4 4 4-4" fill="none" stroke="#fff" stroke-width="1.6"/></svg></div>
  <div class="filter-row">Highest review score<svg width="12" height="12" viewBox="0 0 12 12"><path d="M2 4l4 4 4-4" fill="none" stroke="#fff" stroke-width="1.6"/></svg></div>
  <div class="filter-row">Price high to low<svg width="12" height="12" viewBox="0 0 12 12"><path d="M2 4l4 4 4-4" fill="none" stroke="#fff" stroke-width="1.6"/></svg></div>
  <div class="filter-row">Price low to high<svg width="12" height="12" viewBox="0 0 12 12"><path d="M2 4l4 4 4-4" fill="none" stroke="#fff" stroke-width="1.6"/></svg></div>
  <div class="filter-row">Categories<svg width="12" height="12" viewBox="0 0 12 12"><path d="M2 4l4 4 4-4" fill="none" stroke="#fff" stroke-width="1.6"/></svg></div>
</aside>

<!-- product grid row 1 -->
<article class="abs product" style="left:406px;top:989px">
  <div class="shot"></div><div class="thumb" role="img" aria-label="Amber supplement bottle"></div>
  <div class="rating"><b class="on"></b><b></b><b></b><b></b><b></b><span>6 REVIEWS</span></div>
  <h3>Acai Berry (4000mg x 180 tablets)</h3><div class="cat">Skin Lightening tablets</div><div class="price">£39.99 (GBP)</div><div class="quick">QUICK VIEW</div>
</article>
<article class="abs product" style="left:651px;top:989px">
  <div class="shot"></div><div class="thumb" role="img" aria-label="Amber supplement bottle"></div>
  <div class="rating"><b class="on"></b><b></b><b></b><b></b><b></b><span>6 REVIEWS</span></div>
  <h3>Black Cohosh – 800mg x 90 tablets</h3><div class="cat">Skin Lightening Creams</div><div class="price">£39.99 (GBP)</div><div class="quick">QUICK VIEW</div>
</article>
<article class="abs product" style="left:896px;top:989px">
  <div class="shot"></div><div class="thumb box" role="img" aria-label="Supplement box with capsules"></div>
  <div class="rating"><b class="on"></b><b></b><b></b><b></b><b></b><span>6 REVIEWS</span></div>
  <h3>Acai Berry (4000mg x 180 tablets)</h3><div class="cat">Skin Lightening Soaps</div><div class="price">£39.99 (GBP)</div><div class="quick">QUICK VIEW</div>
</article>
<div class="abs add-cart" style="left:456px;top:1420px">ADD TO CART</div>
<div class="abs add-cart" style="left:701px;top:1420px">ADD TO CART</div>
<div class="abs add-cart" style="left:946px;top:1420px">ADD TO CART</div>

<!-- product grid row 2 -->
<article class="abs product" style="left:406px;top:1491px">
  <div class="shot"></div><div class="thumb" role="img" aria-label="Amber supplement bottle"></div>
  <div class="rating"><b class="on"></b><b></b><b></b><b></b><b></b><span>6 REVIEWS</span></div>
  <h3>Acai Berry (4000mg x 180 tablets)</h3><div class="cat">Skin Lightening tablets</div><div class="price">£39.99 (GBP)</div><div class="quick">QUICK VIEW</div>
</article>
<article class="abs product" style="left:651px;top:1491px">
  <div class="shot"></div><div class="thumb" role="img" aria-label="Amber supplement bottle"></div>
  <div class="rating"><b class="on"></b><b></b><b></b><b></b><b></b><span>6 REVIEWS</span></div>
  <h3>Black Cohosh – 800mg x 90 tablets</h3><div class="cat">Skin Lightening Creams</div><div class="price">£39.99 (GBP)</div><div class="quick">QUICK VIEW</div>
</article>
<article class="abs product" style="left:896px;top:1491px">
  <div class="shot"></div><div class="thumb box" role="img" aria-label="Supplement box with capsules"></div>
  <div class="rating"><b class="on"></b><b></b><b></b><b></b><b></b><span>6 REVIEWS</span></div>
  <h3>Acai Berry (4000mg x 180 tablets)</h3><div class="cat">Skin Lightening Soaps</div><div class="price">£39.99 (GBP)</div><div class="quick">QUICK VIEW</div>
</article>
<div class="abs add-cart" style="left:456px;top:1924px">ADD TO CART</div>
<div class="abs add-cart" style="left:701px;top:1924px">ADD TO CART</div>
<div class="abs add-cart" style="left:946px;top:1924px">ADD TO CART</div>

<!-- contact -->
<section class="abs contact"></section>
<div class="abs contact-photo" role="img" aria-label="Photo of a smiling mature woman with grey hair"></div>
<h2 class="abs contact-title">Contact Us</h2>
<p class="abs contact-lead">Get in touch for expert confidential supplement advice, or for customer services.</p>
<div class="abs contact-col" style="left:453px"><b>Calling from the UK</b><br>0800 000 1234</div>
<div class="abs contact-col" style="left:632px"><b>Calling from Overseas</b><br>+44 800 000 1234</div>
<div class="abs contact-col" style="left:869px">Our team is available<br>Monday - Friday: 8am until 18:00pm<br>Answerphone out of hours</div>
<div class="abs contact-form"><p>To contact us by email, please click the send us a message tab on the bottom.</p></div>
<div class="abs field" style="left:460px;top:2344px;width:289px;height:44px">Enter your name</div>
<div class="abs field" style="left:460px;top:2400px;width:289px;height:44px">Enter your mail address</div>
<div class="abs field" style="left:460px;top:2456px;width:289px;height:44px">Enter your phone number</div>
<div class="abs field" style="left:767px;top:2344px;width:301px;height:156px">Enter your message</div>
<div class="abs send">SEND MESSAGE</div>

<!-- about -->
<section class="abs about"></section>
<div class="abs about-photo" role="img" aria-label="Soft-focus photo of a woman touching her face with eyes closed"></div>
<h2 class="abs about-title">About Us</h2>
<div class="abs about-box">
  <p>I'm a paragraph. Click here to add your own text and edit me. It's easy. Just click "Edit Text" or double click me to add your own content and make changes to the font. Feel free to drag and drop me anywhere you like on your page. I'm a great place for you to tell a story and let your users know a little more about you.</p>
  <p>This is a great space to write long text about your company and your services. You can use this space to go into a little more detail about your company. Talk about your team and what services you provide.</p>
</div>

<!-- footer -->
<footer class="abs footer"></footer>
<div class="abs foot-col" style="left:169px;width:230px">
  <h5>ABOUT US</h5>
  <p>Lunessa is a clinical cosmetics manufacturer providing a safe and natural way of achieving beautiful, strong and healthy eyelashes.</p>
  <span class="pill">READ MORE</span>
</div>
<div class="abs foot-col" style="left:458px;width:230px">
  <h5>WHOLESALE</h5>
  <p>We have salons, stores and online shops all over the world that are stocking our products. We are always interested in working with new vendors. Would you like to become retailer of our products?</p>
  <span class="pill">BECOME A RETAILER</span>
</div>
<div class="abs foot-col" style="left:816px;width:230px">
  <h5>NEWSLETTER</h5>
  <p>Sign up for newsletter and get a -10% discount code for you to use today!</p>
  <div class="email">Enter Email Address</div>
  <span class="pill" style="margin-left:36px">SUBSCRIBE</span>
</div>
<div class="abs bottom">
  <h6>Follow us</h6>
  <div class="follow-icons"><i></i><i></i><i></i><i></i></div>
  <small>Copyright © 2016. All rights reserved.</small>
</div>

</body>
</html>
```